Business Cards for IT Consulting Company (Managed Service Provider)

I am looking to have some business cards printed and would like some designs. We are an IT Consulting company based in Vancouver BC. I would like a nice clean and modern look to the cards. I have uploaded all the versions of my logo so parts can be used as needed. Here is a snippit from our website homepage:

Quillbrook Networks Ltd. is an IT Solutions Partner located in Vancouver BC, Canada. We offer IT solutions and support to customers in the greater Vancouver Area. With expertise in Microsoft platforms, as well as Linux and Mac OSX and over 12 years experience in the IT industry, Quillbrook Networks is dedicated to offering our clients top quality service and products. We take pride in the solutions we offer our customers. The greatest compliment a client can give us is to recommend our services.

Quillbrook Networks Ltd. offers a wide range of IT services from onsite service to remote support and managed service solutions. This allows clients to choose the support path that best suits their company’s needs. Supporting many different sized companies from small to enterprise level over the past 12 years Quillbrook Networks has the experience and expertise needed to ensure things run smoothly. Allowing our clients to focus on doing business.

Revolutionizing the way IT services are delivered.

Quillbrook Networks is dedicated to providing our clients with IT solutions that work and grow with them for years to come. This philosophy helps save money in the long run instead of replacing equipment constantly. Far too often IT solutions are not well thought out and while possibly solving the problem at hand, require replacement due to growth or quality within a very short time frame. Quillbrook Networks takes pride in providing solutions that will last and be able to accommodate growth without the need for replacement.

Industry/Entity Type

Information Technology

Contact Information for Business Card

Quillbrook Networks Ltd.
(Employee Name)
Eml: (Employees Email Address)
Web: quillbrook.me
Ph: 604-555-0148

Font styles to use
Serif
Sans Serif

Requirements
Must have
• The Company logo and company colors.
Nice to have
• - Our tag line: "Revolutionizing IT Services" or "Revolutionizing the way IT services are delivered."
• - Also I really like the idea of nature and technology together blending which is sort of where my logo came from so integrating that somehow onto the business cards would be great.

```html
<!DOCTYPE html>
<html lang="en">
<head>
<meta charset="utf-8">
<title>Quillbrook Networks Ltd. — Business Cards</title>
<link rel="stylesheet" href="https://fonts.googleapis.com/css2?family=Montserrat:wght@500;600;700&display=swap">
<style>
  :root {
    --stage: #2a2a2c;
    --brand-blue: #00a8e8;
    --slate: #58595b;
    --white: #ffffff;
    --soft-white: #f2f2f2;
  }
  * { box-sizing: border-box; margin: 0; padding: 0; }
  html, body {
    width: 1200px; height: 900px; overflow: hidden;
    background: var(--stage);
    font-family: "Montserrat", Arial, sans-serif;
  }
  .canvas {
    position: relative; width: 1200px; height: 900px;
  }
  .card {
    position: absolute; left: 320px; width: 560px; height: 320px;
    overflow: hidden; box-shadow: 0 14px 30px rgba(0,0,0,.45);
  }
  /* Back of card */
  .card--back { top: 90px; background: var(--brand-blue); }
  .tagline {
    position: absolute; left: 0; right: 0; top: 146px;
    text-align: center; color: var(--white);
    font-weight: 600; font-size: 19px; letter-spacing: .6px;
  }
  .back-web {
    position: absolute; right: 30px; bottom: 26px;
    color: var(--white); font-weight: 600; font-size: 12px; letter-spacing: .5px;
  }
  /* Front of card */
  .card--front { top: 490px; background: var(--slate); }
  .corner-panel { position: absolute; right: 0; top: 0; }
  .brand {
    position: absolute; left: 40px; top: 112px;
    display: flex; align-items: center; gap: 14px;
  }
  .brand-mark { width: 26px; height: 26px; background: var(--brand-blue); }
  .brand-name {
    color: var(--white); font-weight: 600; font-size: 25px; letter-spacing: .3px;
  }
  .person { position: absolute; left: 40px; top: 190px; }
  .person-name {
    color: var(--brand-blue); font-weight: 700; font-size: 19px; letter-spacing: 1.5px;
  }
  .person-role {
    color: var(--white); font-weight: 700; font-size: 11px; letter-spacing: 1px; margin-top: 2px;
  }
  .accent-tab {
    position: absolute; left: 0; top: 196px; width: 22px; height: 12px;
    display: flex;
  }
  .accent-tab span { flex: 1; }
  .accent-tab .tab-white { background: var(--soft-white); }
  .accent-tab .tab-blue { background: var(--brand-blue); }
  .contact-list { position: absolute; left: 40px; top: 244px; list-style: none; }
  .contact-list li {
    display: flex; align-items: center; gap: 9px;
    color: var(--white); font-weight: 600; font-size: 12.5px; letter-spacing: .4px;
    height: 20px;
  }
  .contact-list svg { width: 11px; height: 11px; flex: none; }
</style>
</head>
<body>
<main class="canvas">

  <section class="card card--back" aria-label="Card back">
    <p class="tagline">Revolutionizing IT Services</p>
    <p class="back-web">www.quillbrook.me</p>
  </section>

  <section class="card card--front" aria-label="Card front">
    <svg class="corner-panel" width="200" height="230" viewBox="0 0 200 230" aria-hidden="true">
      <polygon points="90,0 200,0 200,230" fill="var(--white)"/>
    </svg>

    <div class="brand">
      <span class="brand-mark"></span>
      <span class="brand-name">Quillbrook Networks Ltd.</span>
    </div>

    <div class="accent-tab" aria-hidden="true">
      <span class="tab-white"></span><span class="tab-blue"></span>
    </div>

    <div class="person">
      <p class="person-name">MARLA PENNER</p>
      <p class="person-role">DIRECTOR</p>
    </div>

    <ul class="contact-list">
      <li>
        <svg viewBox="0 0 12 12" aria-hidden="true"><path d="M3 1 L5 3 L4 4.5 Q5 7 7.5 8 L9 7 L11 9 L9.5 11 Q2 10 1 2.5 Z" fill="var(--brand-blue)"/></svg>
        604-555-0148
      </li>
      <li>
        <svg viewBox="0 0 12 12" aria-hidden="true"><rect x="1" y="2.5" width="10" height="7" fill="none" stroke="var(--brand-blue)" stroke-width="1.2"/><path d="M1 2.5 L6 6.5 L11 2.5" fill="none" stroke="var(--brand-blue)" stroke-width="1.2"/></svg>
        info@marlapenner.com
      </li>
      <li>
        <svg viewBox="0 0 12 12" aria-hidden="true"><circle cx="6" cy="6" r="4.8" fill="none" stroke="var(--brand-blue)" stroke-width="1.2"/><ellipse cx="6" cy="6" rx="2" ry="4.8" fill="none" stroke="var(--brand-blue)" stroke-width="1"/><line x1="1.2" y1="6" x2="10.8" y2="6" stroke="var(--brand-blue)" stroke-width="1"/></svg>
        www.quillbrook.me
      </li>
    </ul>
  </section>

</main>
</body>
</html>
```